ULMIRA card Technical Architecture

Hello everyone ULMIRA: It is a consulting firm in Architecture and Construction. I require a card duplexing, sober, elegant, classic but not boring. Update 1: Use the following data for the card. Name: Gonzalo Pereda Mauricio Villalta Position: COO Twitter: @ulmiraAT Homepage: ulmira-example.com home address not include the participation of all thank you.

Target Market(s)

Construction companies, Architects and Consulting Engineers

Industry/Entity Type

Consulting

Contact Information for Business Card

Los campos que debe tener:
Nombre, Cargo, email, homepage y twitter

Font styles to use
Serif
Sans Serif
Other font styles liked:
• Me gustan playfair display, open sans y roboto, pero estoy sujeto a sus propuestas

Requirements
Must have
• Colors: Present combined proposals in white, red, gray and black Update 1: The two names must be clearly differentiated from the two surnames
Nice to have
• They are free to present their best proposals. I will bring them immediate feedback to the extent you can go see their designs. Complete data for card and logo files will give the winner the

```html
<!DOCTYPE html>
<html lang="es">
<head>
<meta charset="utf-8">
<title>ULMIRA – Tarjeta de presentación</title>
<link href="https://fonts.googleapis.com/css2?family=Montserrat:wght@400;500;700&display=swap" rel="stylesheet">
<style>
  :root {
    --stage: #2a2a2a;
    --card: #0b0b0b;
    --white: #ffffff;
    --soft-white: #e6e6e6;
    --grey: #8a8a8a;
    --red: #c8232b;
  }
  * { margin: 0; padding: 0; box-sizing: border-box; }
  html, body { width: 1200px; height: 900px; overflow: hidden; }
  body {
    background: var(--stage);
    font-family: "Montserrat", Arial, sans-serif;
    position: relative;
  }
  .card {
    position: absolute;
    width: 560px;
    height: 320px;
    background: var(--card);
    border-radius: 20px;
    box-shadow: 0 18px 40px rgba(0,0,0,0.55);
    overflow: hidden;
  }
  .card--front { left: 70px; top: 90px; }
  .card--back { left: 570px; top: 490px; }

  /* Front */
  .brand {
    position: absolute;
    left: 0; right: 0; top: 108px;
    text-align: center;
  }
  .brand__name {
    color: var(--white);
    font-weight: 400;
    font-size: 58px;
    letter-spacing: 18px;
    padding-left: 18px;
    line-height: 1;
  }
  .brand__rule {
    width: 330px;
    height: 1px;
    background: var(--grey);
    margin: 12px auto 8px;
  }
  .brand__tagline {
    color: var(--red);
    font-size: 15px;
    font-weight: 500;
    letter-spacing: 6px;
    padding-left: 6px;
  }
  .social {
    position: absolute;
    right: 26px; bottom: 22px;
    display: flex; align-items: center; gap: 8px;
    color: var(--soft-white);
    font-size: 13px;
  }
  .social__dot {
    width: 12px; height: 12px;
    border-radius: 50%;
    background: var(--soft-white);
  }

  /* Back */
  .back-brand {
    position: absolute;
    left: 0; width: 300px; top: 0; bottom: 0;
    display: flex; align-items: center; justify-content: center;
    color: var(--red);
    font-weight: 700;
    font-size: 40px;
    letter-spacing: 6px;
  }
  .divider {
    position: absolute;
    left: 300px; top: 50px; bottom: 50px;
    width: 1px;
    background: linear-gradient(to bottom, transparent, var(--grey) 25%, var(--grey) 75%, transparent);
  }
  .details {
    position: absolute;
    left: 326px; top: 58px; right: 18px;
    color: var(--white);
  }
  .person__given, .person__family {
    font-weight: 700;
    font-size: 20px;
    line-height: 1.15;
  }
  .person__role {
    font-size: 12px;
    color: var(--soft-white);
    margin-bottom: 8px;
  }
  .contact { list-style: none; margin-top: 10px; }
  .contact__item {
    display: flex; align-items: center; gap: 8px;
    font-size: 12.5px;
    color: var(--soft-white);
    line-height: 1.7;
    white-space: nowrap;
  }
  .contact__icon { width: 11px; height: 11px; flex: none; }
</style>
</head>
<body>

  <section class="card card--front" aria-label="Tarjeta, cara frontal">
    <div class="brand">
      <div class="brand__name">ULMIRA</div>
      <div class="brand__rule"></div>
      <div class="brand__tagline">ARQUITECTURA TÉCNICA</div>
    </div>
    <div class="social">
      <span class="social__dot"></span>
      <span>@ulmiraAT</span>
    </div>
  </section>

  <section class="card card--back" aria-label="Tarjeta, cara posterior">
    <div class="back-brand">ULMIRA</div>
    <div class="divider"></div>
    <div class="details">
      <div class="person__given">Mauricio Gonzalo</div>
      <div class="person__role">COO</div>
      <div class="person__family">Pereda Villalta</div>
      <div class="person__role">Director de Operaciones</div>
      <ul class="contact">
        <li class="contact__item">
          <svg class="contact__icon" viewBox="0 0 24 24" fill="#e6e6e6"><path d="M6.6 10.8a15.1 15.1 0 0 0 6.6 6.6l2.2-2.2c.3-.3.7-.4 1-.2 1.1.4 2.3.6 3.6.6.6 0 1 .4 1 1V20c0 .6-.4 1-1 1C10.6 21 3 13.4 3 4c0-.6.4-1 1-1h3.5c.6 0 1 .4 1 1 0 1.3.2 2.5.6 3.6.1.3 0 .7-.2 1z"/></svg>
          <span>(+570) 555 010 2030</span>
        </li>
        <li class="contact__item">
          <svg class="contact__icon" viewBox="0 0 24 24" fill="none" stroke="#e6e6e6" stroke-width="2"><rect x="3" y="5" width="18" height="14" rx="1"/><path d="M3 6l9 7 9-7"/></svg>
          <span>info@ulmira-example.com</span>
        </li>
        <li class="contact__item">
          <svg class="contact__icon" viewBox="0 0 24 24" fill="none" stroke="#e6e6e6" stroke-width="2"><circle cx="12" cy="12" r="9"/><path d="M3 12h18M12 3c3 3 3 15 0 18M12 3c-3 3-3 15 0 18"/></svg>
          <span>www.ulmira-example.com</span>
        </li>
      </ul>
    </div>
  </section>

</body>
</html>
```